New Interrior Decoration company needs new website

We need a website for our new company specialising in interior decoration to residential and commercial markets.
We supply and install decorative and printed films for office and home decoration such as feature walls.
We would like to keep the design simple and clean.

Target Market(s)

Architects and interior designaers

Industry/Entity Type

It Company

Number of Pages Required

5+ page

Font styles to use
Sans Serif

Requirements
Must have
• Home page,
• Services/products page (split into commercial and residential)
• Gallery (split into commercial and residential)
• contact form and page
Nice to have
• Very clean and minimalistic design.

```html
<!DOCTYPE html>
<html lang="en">
<head>
<meta charset="utf-8">
<title>Halden Interiors</title>
<link href="https://fonts.googleapis.com/css2?family=Montserrat:wght@300;400;500;600;700&display=swap" rel="stylesheet">
<style>
:root{
  --blue:#2469b6;
  --blue-dark:#1d5aa0;
  --ink:#1b1b1b;
  --text:#555;
  --muted:#8a8a8a;
  --card:#eeeeee;
  --white:#fff;
  --footer:#2a6cbd;
  --line:#d7d7d7;
}
*{margin:0;padding:0;box-sizing:border-box}
html,body{width:1200px;height:3041px;overflow:hidden}
body{font-family:"Montserrat",Arial,sans-serif;color:var(--text);background:var(--white);position:relative}
.abs{position:absolute}
/* header */
.site-header{position:absolute;left:0;top:0;width:1200px;height:120px;background:var(--white)}
.brand{position:absolute;left:100px;top:34px;display:flex;align-items:center;gap:12px}
.brand-mark{width:52px;height:52px;background:var(--blue)}
.brand-name{font-weight:700;font-size:29px;line-height:27px;color:#222;text-transform:uppercase;letter-spacing:-.5px}
.main-nav{position:absolute;right:100px;top:58px;display:flex;gap:40px}
.main-nav a{font-size:13px;font-weight:600;color:#222;text-decoration:none;text-transform:uppercase;display:flex;align-items:center;gap:10px}
.main-nav a.active{color:var(--blue)}
.main-nav a:not(.active)::before{content:"";width:5px;height:5px;border-radius:50%;background:var(--blue)}
/* hero */
.hero{position:absolute;left:0;top:120px;width:1200px;height:548px;background:linear-gradient(180deg,#5c6a77 0%,#7f8a92 40%,#3c3f44 75%,#2b2d31 100%)}
.hero-text{position:absolute;left:0;width:1200px;text-align:center;color:var(--white)}
.hero-kicker{top:188px;font-size:24px;font-weight:400;letter-spacing:.5px}
.hero-title{top:225px;font-size:41px;font-weight:600;letter-spacing:.5px}
.hero-arrow{position:absolute;top:233px;width:42px;height:42px;border-radius:50%;background:rgba(255,255,255,.25)}
/* section titles */
.section-title{position:absolute;left:0;width:1200px;text-align:center;font-size:30px;font-weight:700;color:var(--ink);text-transform:uppercase}
.section-title span{color:var(--blue)}
.title-rule{position:absolute;left:535px;width:130px;height:1px;background:var(--line)}
.title-rule::after{content:"";position:absolute;left:62px;top:-3px;width:7px;height:7px;border-radius:50%;background:var(--blue)}
/* services */
.service-card{position:absolute;top:878px;width:312px;height:325px;background:var(--card);text-align:center}
.service-photo{position:absolute;left:82px;top:-75px;width:148px;height:148px;border-radius:50%;border:5px solid var(--white);box-shadow:0 0 0 1px #ccc}
.service-name{position:absolute;left:0;top:99px;width:100%;font-size:17px;font-weight:500;color:var(--ink);text-transform:uppercase}
.service-rule{position:absolute;left:106px;top:135px;width:100px;height:1px;background:#d0d0d0}
.service-copy{position:absolute;left:40px;top:150px;width:232px;font-size:12.5px;line-height:23px;color:var(--muted)}
.btn{position:absolute;left:83px;top:242px;width:146px;height:45px;background:var(--blue);color:var(--white);font-size:13.5px;font-weight:500;display:flex;align-items:center;justify-content:center;text-transform:uppercase}
/* banner */
.banner{position:absolute;left:0;top:1267px;width:1200px;height:456px;background:linear-gradient(180deg,#3d74b6 0%,#336cb0 60%,#2c64a7 100%)}
.banner-sofa{position:absolute;left:235px;top:245px;width:745px;height:170px;border-radius:40px 40px 10px 10px;background:rgba(120,170,225,.45)}
.banner-title{position:absolute;left:0;top:63px;width:1200px;text-align:center;font-size:44px;font-weight:400;line-height:46px;color:var(--white)}
.banner-copy{position:absolute;left:225px;top:183px;width:750px;text-align:center;font-size:14px;line-height:27px;color:#e6eef8}
.btn-ghost{position:absolute;left:491px;top:293px;width:218px;height:50px;border:1px solid rgba(255,255,255,.8);color:var(--white);font-size:18px;font-weight:500;display:flex;align-items:center;justify-content:center;letter-spacing:.5px}
/* gallery */
.gallery-item{position:absolute;width:238px}
/* testimonial */
.testimonials{position:absolute;left:0;top:2353px;width:1200px;height:367px;background:linear-gradient(180deg,#e4dcdf 0%,#dcd9de 55%,#cfd2d8 100%)}
.testimonial-quote{position:absolute;left:200px;top:118px;width:800px;text-align:center;font-size:12px;line-height:23px;color:#555}
.quote-mark{position:absolute;font-size:60px;font-weight:700;color:#b9b9c0;line-height:1}
.testimonial-author{position:absolute;left:0;top:224px;width:1200px;text-align:center;font-size:12px;color:#333}
.testimonial-author span{color:var(--blue)}
.dots{position:absolute;left:560px;top:280px;display:flex;gap:4px}
.dots i{width:16px;height:16px;border-radius:50%;background:#666;display:block}
.dots i.on{background:transparent;border:2px solid #666}
/* footer */
.site-footer{position:absolute;left:0;top:2720px;width:1200px;height:321px;background:var(--footer);color:var(--white)}
.footer-col{position:absolute;top:0;height:202px;padding-top:42px}
.footer-col+.footer-col{border-left:1px solid rgba(255,255,255,.15)}
.footer-col h4{font-size:16px;font-weight:600;text-transform:uppercase;margin-bottom:18px;letter-spacing:.3px}
.footer-col li{list-style:none;font-size:13px;line-height:30px}
.contact-line{display:flex;align-items:center;gap:12px}
.footer-col p{font-size:13px;line-height:20px}
.socials{display:flex;gap:6px;margin-top:16px}
.socials i{width:37px;height:37px;border-radius:50%;border:2px solid var(--white);display:block;background:#3b7fcb}
.socials i:last-child{background:#d9483b}
.footer-rule{position:absolute;left:100px;top:250px;width:1000px;height:1px;background:rgba(255,255,255,.35)}
.copyright{position:absolute;left:100px;top:272px;font-size:12px}
</style>
</head>
<body>

<header class="site-header">
  <div class="brand"><div class="brand-mark"></div><div class="brand-name">Halden<br>Interiors</div></div>
  <nav class="main-nav">
    <a class="active">Home</a><a>Services</a><a>Products</a><a>Gallery</a><a>Contact us</a>
  </nav>
</header>

<section class="hero" role="img" aria-label="Photo of a bright bedroom with a yellow bedspread, white furniture and large windows">
  <div class="hero-arrow" style="left:22px"></div>
  <div class="hero-arrow" style="right:22px"></div>
  <svg class="abs" style="left:36px;top:245px" width="14" height="18"><path d="M10 2 3 9l7 7" fill="none" stroke="#fff" stroke-width="2"/></svg>
  <svg class="abs" style="right:36px;top:245px" width="14" height="18"><path d="M4 2l7 7-7 7" fill="none" stroke="#fff" stroke-width="2"/></svg>
  <div class="hero-text hero-kicker">WE SPECIALISE IN INTERIOR DECORATION TO</div>
  <div class="hero-text hero-title">RESIDENTIAL AND COMMERCIAL MARKETS</div>
</section>

<h2 class="section-title" style="top:706px">Our services <span>we provide</span></h2>
<div class="title-rule" style="top:763px"></div>

<article class="service-card" style="left:101px">
  <div class="service-photo" role="img" aria-label="Office interior with wood panel wall" style="background:linear-gradient(135deg,#4e6f8f,#8a5a3c)"></div>
  <h3 class="service-name">Office Decoration</h3><div class="service-rule"></div>
  <p class="service-copy">Sed ut perspiciatis unde omnis iste natus error sit voluptatem accusantium doloremque laudantium.</p>
  <div class="btn">Read more&nbsp;»</div>
</article>
<article class="service-card" style="left:444px">
  <div class="service-photo" role="img" aria-label="Living room with patterned red feature wall" style="background:linear-gradient(135deg,#7a3a44,#c08a8a)"></div>
  <h3 class="service-name">Home Decoration</h3><div class="service-rule"></div>
  <p class="service-copy">Sed ut perspiciatis unde omnis iste natus error sit voluptatem accusantium doloremque laudantium.</p>
  <div class="btn">Read more&nbsp;»</div>
</article>
<article class="service-card" style="left:788px">
  <div class="service-photo" role="img" aria-label="Stone textured feature wall" style="background:linear-gradient(135deg,#5e6e64,#a3aca2)"></div>
  <h3 class="service-name">Feature Walls</h3><div class="service-rule"></div>
  <p class="service-copy">Sed ut perspiciatis unde omnis iste natus error sit voluptatem accusantium doloremque laudantium.</p>
  <div class="btn">Read more&nbsp;»</div>
</article>

<section class="banner">
  <div class="banner-sofa" role="img" aria-label="Photo of a sofa against a wall, tinted blue"></div>
  <h2 class="banner-title">We Specialise in Interior Decoration to<br>Residential and Commercial Markets</h2>
  <p class="banner-copy">Ut enim ad minim veniam, quis nostrud exercitation ullamco laboris nisi ut aliquip ex ea commodo consequat. Duis aute irure dolor in reprehenderit in voluptate velit esse cillum dolore eu fugiat nulla pariatur. Excepteur sint occaecat cupidatat non proident, sunt in culpa qui officia deserunt mollit anim id est laborum</p>
  <div class="btn-ghost">VIEW MORE</div>
</section>

<h2 class="section-title" style="top:1760px">Our <span>gallery</span></h2>
<div class="title-rule" style="top:1816px"></div>

<div class="gallery-item" role="img" aria-label="Commercial reception with curved wooden counter" style="left:103px;top:1851px;height:210px;background:linear-gradient(135deg,#9aa0a3,#6a5440)"></div>
<div class="gallery-item" role="img" aria-label="Grey living room with pendant lamp" style="left:356px;top:1851px;height:210px;background:linear-gradient(135deg,#5b5f60,#c9cdcc)"></div>
<div class="gallery-item" role="img" aria-label="Lounge with yellow-green printed wall" style="left:608px;top:1851px;height:210px;background:linear-gradient(135deg,#c6cf7a,#e4e7cf)"></div>
<div class="gallery-item" role="img" aria-label="Room with dark green wall and sideboard" style="left:862px;top:1851px;height:210px;background:linear-gradient(135deg,#6f7b6d,#b7b9ae)"></div>
<div class="gallery-item" role="img" aria-label="Retail shelving in yellow and white" style="left:103px;top:2076px;height:209px;background:linear-gradient(135deg,#d8a63a,#efe7d6)"></div>
<div class="gallery-item" role="img" aria-label="Olive wall with low cabinet and vases" style="left:356px;top:2076px;height:209px;background:linear-gradient(135deg,#6f6a3c,#b2ab7e)"></div>
<div class="gallery-item" role="img" aria-label="Multicoloured wood panel wall with red chairs" style="left:608px;top:2076px;height:209px;background:linear-gradient(135deg,#b58e5c,#c0392b)"></div>
<div class="gallery-item" role="img" aria-label="Dark red room with lounge chair and lamp" style="left:862px;top:2076px;height:209px;background:linear-gradient(135deg,#5a1f14,#2a1410)"></div>

<section class="testimonials" role="img" aria-label="Faded photo of a city skyline by the sea">
  <h2 class="section-title" style="top:43px;font-size:28px">What clients say</h2>
  <svg class="abs" style="left:596px;top:88px" width="7" height="7"><circle cx="3.5" cy="3.5" r="3" fill="#2469b6"/></svg>
  <div class="quote-mark" style="left:150px;top:112px">“</div>
  <div class="quote-mark" style="left:1000px;top:150px">”</div>
  <p class="testimonial-quote">La dermocosmesi si occupe attraverso l' utilizzo di prodotti tecnologicamente innovativi e sostanze polifunzionali di garantire e mantenere lo stato di salute, di benessere e quindi di bellezza della pelle. Fin dall' antichità sia l'uomo che la donna si sono occupati ampiamente del proprio aspetto fisico impiegando tempo e risorse, indipendentemente dal ceto sociale</p>
  <p class="testimonial-author"><span>- Mark Ellis,</span> Businessman</p>
  <div class="dots"><i class="on"></i><i></i><i></i><i></i></div>
</section>

<footer class="site-footer">
  <div class="footer-col" style="left:100px;width:175px">
    <h4>Company</h4>
    <ul><li>Home</li><li>Services</li><li>Products</li><li>Gallery</li><li>Contact us</li></ul>
  </div>
  <div class="footer-col" style="left:250px;width:205px;padding-left:26px">
    <h4>Services</h4>
    <ul><li>Office Decoration</li><li>Home Decoration</li><li>Features Walls</li><li>Other Services</li></ul>
  </div>
  <div class="footer-col" style="left:455px;width:290px;padding-left:43px">
    <h4>Get in touch</h4>
    <ul>
      <li class="contact-line"><svg width="14" height="14" viewBox="0 0 24 24"><path fill="#fff" d="M6.6 10.8a15 15 0 0 0 6.6 6.6l2.2-2.2c.3-.3.7-.4 1-.2 1.1.4 2.3.6 3.6.6.6 0 1 .4 1 1V20c0 .6-.4 1-1 1A17 17 0 0 1 3 4c0-.6.4-1 1-1h3.5c.6 0 1 .4 1 1 0 1.3.2 2.5.6 3.6.1.3 0 .7-.2 1z"/></svg>Call us on (01) 55501234</li>
      <li class="contact-line"><svg width="14" height="12" viewBox="0 0 24 20"><path fill="#fff" d="M2 2h20v16H2zM3 3.5V5l9 6 9-6V3.5z"/></svg>info@haldenstudio.com</li>
    </ul>
  </div>
  <div class="footer-col" style="left:745px;width:145px;padding-left:24px">
    <h4>Why us</h4>
    <ul><li>Customers</li><li>Team</li><li>FAQ</li><li>Contact</li></ul>
  </div>
  <div class="footer-col" style="left:890px;width:210px;padding-left:36px">
    <h4>Folllow us</h4>
    <p>Please connect with us on</p>
    <div class="socials"><i aria-label="Social link"></i><i aria-label="Social link"></i><i aria-label="Social link"></i><i aria-label="Social link"></i></div>
  </div>
  <div class="footer-rule"></div>
  <p class="copyright">© 2016 Company Name&nbsp; All right reserved&nbsp; Term of Use</p>
</footer>

</body>
</html>
```